Business Card Design

We like to use greens as you will see in our logo (but not TOO much green). We are a Dental Clinic in a somewhat eccentric community. We do not like the dated sharp designs which we see many dentists use. We're looking for something bright and fresh while still maintaining the integrity of the profession. Elegance is not necessarily what we are going for... we need for the design to be "mature" but also up-lifting.

See our logo.
Updates

Project Deadline Extended
Reason: We have 5 designs which we like. But we'd like to see a few more before committing to a design.

Project Deadline Extended
Reason: We are awaiting revisions to this project. We are still welcoming designs while we wait to see if designers are able to provide to us the revisions we require in order to proceed with a selection.

Target Market(s)

Younger families - ages late 20's to early 40's

Industry/Entity Type

Business

Contact Information for Business Card

Corwel T. Banfry DDS 2730 W. Halvert Rd. Ste. 7 Royal Oak, MI 48391 (248)555-0174 FX (248)555-0189 info@BrightwellDentalCareMi.com BrigthwellDentalCareMi.com on the back of the card we need an appointment reminder (For____ Date___ Time____) with "If you are unable to keep your appointment, kindly give 48 hours notice" at the bottom. No use of teeth in the design. DOUBLE SIDED DESIGN

Requirements
Should not have
• The use of pictures of teeth

```html
<!DOCTYPE html>
<html lang="en">
<head>
<meta charset="utf-8">
<title>Brightwell Dental Care – Business Card</title>
<link href="https://fonts.googleapis.com/css2?family=Open+Sans:wght@400;600;700&family=Tinos:ital,wght@0,700;1,400&display=swap" rel="stylesheet">
<style>
  :root {
    --bg: #ececea;
    --card: #ffffff;
    --green-dark: #2f7a16;
    --green-mid: #3d8f1c;
    --green-lime: #8fd21d;
    --ink: #3a3a3a;
    --ink-soft: #5a5a5a;
    --line: #9a9a9a;
  }
  * { margin: 0; padding: 0; box-sizing: border-box; }
  html, body { width: 1200px; height: 492px; overflow: hidden; }
  body {
    background: var(--bg);
    font-family: "Open Sans", Arial, sans-serif;
    color: var(--ink);
    position: relative;
  }
  .card {
    position: absolute;
    top: 96px;
    width: 540px;
    height: 300px;
    background: var(--card);
    box-shadow: 0 6px 18px rgba(0,0,0,.18);
    overflow: hidden;
  }
  .card--front { left: 36px; }
  .card--back { left: 624px; }

  /* brand */
  .brand { display: flex; align-items: center; gap: 10px; color: var(--green-dark); font-weight: 600; }
  .brand__dot { width: 18px; height: 18px; border-radius: 50%; background: var(--green-lime); flex: none; }
  .brand__name { line-height: 1.05; }
  .card--front .brand { position: absolute; left: 0; right: 0; top: 52px; justify-content: center; font-size: 30px; }
  .card--back .brand { position: absolute; left: 28px; top: 30px; font-size: 22px; }

  /* front */
  .doctor {
    position: absolute; left: 70px; top: 160px;
    font-size: 17px; font-weight: 700; color: var(--green-dark);
  }
  .doctor__title { color: var(--green-lime); font-size: 14px; }
  .address {
    position: absolute; left: 40px; top: 200px; width: 226px;
    text-align: right; font-size: 12.5px; line-height: 1.45; color: var(--ink);
  }
  .divider { position: absolute; left: 280px; top: 140px; width: 1px; height: 86px; background: #cfcfcf; }
  .contacts { position: absolute; left: 290px; top: 140px; list-style: none; font-size: 12.5px; line-height: 21px; }
  .contacts li { display: flex; align-items: center; gap: 5px; }
  .contacts svg { width: 11px; height: 11px; fill: var(--ink); flex: none; }
  .bands { position: absolute; left: 0; bottom: 0; width: 540px; height: 70px; }

  /* back */
  .appt { position: absolute; left: 28px; right: 28px; top: 100px; font-size: 14px; color: var(--ink-soft); }
  .appt__title {
    font-family: "Tinos", "Times New Roman", serif; font-weight: 700;
    font-size: 16px; color: var(--green-dark); letter-spacing: .3px;
    border-bottom: 1px solid var(--line); padding-bottom: 3px; width: 340px;
  }
  .field-row { display: flex; align-items: flex-end; gap: 8px; margin-top: 12px; }
  .rule { border-bottom: 1px dotted var(--line); height: 14px; }
  .box { width: 92px; height: 22px; border: 1px solid #777; }
  .box--sm { width: 32px; height: 20px; }
  .days { display: flex; align-items: center; gap: 6px; font-weight: 700; font-size: 13.5px; color: #4a4a4a; margin-top: 10px; }
  .notice {
    position: absolute; left: 28px; right: 20px; bottom: 18px;
    font-family: "Tinos", "Times New Roman", serif; font-style: italic;
    font-size: 14.5px; color: var(--ink-soft);
  }
</style>
</head>
<body>

<section class="card card--front" aria-label="Business card front">
  <div class="brand">
    <span class="brand__dot"></span>
    <span class="brand__name">Brightwell Dental Care</span>
  </div>

  <p class="doctor">Corwel T. Banfry, <span class="doctor__title">DDS</span></p>
  <p class="address">2730 W. Halvert Rd. Ste. 7<br>Royal Oak, MI 48391</p>

  <div class="divider"></div>
  <ul class="contacts">
    <li><svg viewBox="0 0 12 12"><path d="M3 1l2 2.5-1.2 1.2a6 6 0 003.5 3.5L8.5 7 11 9l-1.2 2C5 11 1 7 1 2.2z"/></svg>(248)555-0174</li>
    <li><svg viewBox="0 0 12 12"><rect x="1" y="5" width="10" height="5" rx="1"/><rect x="3" y="1" width="6" height="4"/></svg>(248)555-0189</li>
    <li><svg viewBox="0 0 12 12"><path d="M1 3h10v6H1z M1 3l5 3.5L11 3" fill="none" stroke="#3a3a3a" stroke-width="1.2"/></svg>info@BrightwellDentalCareMi.com</li>
    <li><svg viewBox="0 0 12 12"><circle cx="6" cy="6" r="5" fill="none" stroke="#3a3a3a" stroke-width="1.2"/><path d="M1 6h10M6 1v10M3.5 2.5q-1.5 3.5 0 7M8.5 2.5q1.5 3.5 0 7" fill="none" stroke="#3a3a3a" stroke-width=".9"/></svg>www.BrigthwellDentalCareMi.com</li>
  </ul>

  <svg class="bands" viewBox="0 0 540 70" preserveAspectRatio="none" aria-hidden="true">
    <polygon points="290,46 540,20 540,60 270,70" fill="var(--green-mid)"/>
    <polygon points="0,70 0,58 284,46 264,70" fill="var(--green-lime)"/>
  </svg>
</section>

<section class="card card--back" aria-label="Appointment reminder card back">
  <div class="brand">
    <span class="brand__dot"></span>
    <span class="brand__name">Brightwell Dental Care</span>
  </div>

  <div class="appt">
    <h2 class="appt__title">YOUR APPOINTMENT</h2>
    <div class="field-row"><span>Name :</span><span class="rule" style="flex:1"></span></div>
    <div class="field-row">
      <span>Date :</span><span class="rule" style="width:96px"></span>
      <span>&nbsp;Time :</span><span class="rule" style="width:90px"></span><span>am / pm</span>
    </div>
    <div class="field-row">
      <span>Next Appointment</span><span class="box"></span><span class="box" style="margin-left:26px"></span>
    </div>
    <div class="days">
      <span>MON</span><span class="box box--sm"></span>
      <span>TUE</span><span class="box box--sm"></span>
      <span>WED</span><span class="box box--sm"></span>
      <span>THU</span><span class="box box--sm"></span>
      <span>FRI</span><span class="box box--sm"></span>
      <span>SAT</span><span class="box box--sm"></span>
    </div>
  </div>

  <p class="notice">If you are unable to keep your appointment, kindly give 48 hours notice</p>
</section>

</body>
</html>
```